Help design website for "Brightwater Civic Advisors" to advance the common good

Here is the Google doc link that lays out the design:

https://files.plumrivet.example/sheet/d/7QmTzR2wLx9KpVbN4hJcY8sEaUoFdG3iXkMnPq5rWt6/edit?usp=sharing

Here is the Google drive folder with the logos and photos: https://vault.plumrivet.example/open?id=4HkWp9LzQe2TxRvN8mBaYc3DsUoJfG6

The testimonials are being gathered and will be shared by Friday, 1/4.

The winner will also have to migrate the coding files to my hosting site.

Thank you for your help! Looking forward to seeing your designs.

Target Market(s)

Prospective clients

Industry/Entity Type

Non Profit

Coding

Coded - Design and coding required

Number of Pages Required

5+ page

Requirements
Must have
• Noted in the Google doc regarding layout.
Nice to have

```html
<!DOCTYPE html>
<html lang="en">
<head>
<meta charset="UTF-8">
<title>Contact | Brightwater Civic Advisors</title>
<link href="https://fonts.googleapis.com/css2?family=Montserrat:wght@400;500&family=Open+Sans:wght@400&family=Poppins:wght@600;700&display=swap" rel="stylesheet">
<style>
  :root {
    --brand-blue: #3d8bce;
    --ink: #111111;
    --body-text: #2a2a2a;
    --field-border: #c4c4c4;
    --field-text: #3a3a3a;
    --footer-dark: #272830;
    --pattern-tint: #f3f3f3;
    --white: #ffffff;
  }
  * { box-sizing: border-box; margin: 0; padding: 0; }
  html, body { width: 982px; height: 1200px; overflow: hidden; background: var(--white); }
  .page { position: relative; width: 982px; height: 1200px; overflow: hidden; font-family: "Open Sans", sans-serif; }

  .site-header { position: absolute; top: 0; left: 0; width: 982px; height: 114px; background: var(--brand-blue); }
  .brand { position: absolute; display: flex; align-items: center; gap: 12px; color: var(--white); font-family: "Montserrat", sans-serif; font-weight: 500; text-transform: uppercase; }
  .brand-mark { background: var(--white); }
  .header-brand { left: 118px; top: 30px; font-size: 16px; letter-spacing: 4px; line-height: 20px; }
  .header-brand .brand-mark { width: 46px; height: 46px; }
  .cta-button { position: absolute; left: 602px; top: 29px; width: 262px; height: 34px; border: 2px solid var(--white); color: var(--white); font-family: "Poppins", sans-serif; font-weight: 700; font-size: 11.5px; display: flex; align-items: center; justify-content: center; text-decoration: none; }
  .main-nav a { position: absolute; top: 83px; color: var(--white); font-family: "Poppins", sans-serif; font-weight: 700; font-size: 11.2px; text-decoration: none; }
  .main-nav a.is-current { border-bottom: 1px solid var(--white); padding-bottom: 2px; }

  .page-title { position: absolute; top: 152px; width: 100%; text-align: center; font-family: "Poppins", sans-serif; font-weight: 600; font-size: 26px; color: var(--ink); }
  .portrait { position: absolute; left: 408px; top: 216px; width: 168px; height: 168px; border-radius: 50%; border: 3px solid #d8d8d8; box-shadow: 0 6px 18px rgba(0,0,0,0.18); background: radial-gradient(circle at 50% 45%, #8a6a55 0%, #3b3a40 55%, #5a6c7c 100%); }
  .section-heading { position: absolute; width: 100%; text-align: center; font-family: "Poppins", sans-serif; font-weight: 600; color: var(--ink); }
  .rates-heading { top: 421px; font-size: 18px; }
  .consult-heading { top: 516px; font-size: 19px; }
  .section-text { position: absolute; width: 100%; text-align: center; font-size: 11.4px; color: var(--body-text); }
  .rates-text { top: 453px; }
  .consult-text { top: 550px; }

  .field { position: absolute; border: 2px solid var(--field-border); border-radius: 3px; font-size: 10.4px; color: var(--field-text); padding: 0 14px; display: flex; align-items: center; text-transform: uppercase; }
  .field-message { align-items: flex-start; padding-top: 11px; }
  .submit-button { position: absolute; left: 442px; top: 836px; width: 101px; height: 35px; background: var(--brand-blue); color: var(--white); font-family: "Poppins", sans-serif; font-weight: 700; font-size: 14px; display: flex; align-items: center; justify-content: center; }

  .footer-band { position: absolute; left: 0; top: 884px; width: 982px; height: 150px; background: var(--pattern-tint); }
  .footer-shape { position: absolute; left: 0; top: 884px; }
  .footer-brand { left: 118px; top: 1070px; font-size: 21px; letter-spacing: 5px; line-height: 26px; }
  .footer-brand .brand-mark { width: 58px; height: 58px; background: var(--brand-blue); }
  .footer-divider { position: absolute; left: 500px; top: 1043px; width: 1px; height: 117px; background: #4a4b54; }
  .footer-menu-title { position: absolute; left: 549px; top: 1057px; color: var(--white); font-family: "Poppins", sans-serif; font-weight: 700; font-size: 10.4px; }
  .footer-links { position: absolute; left: 549px; top: 1086px; color: var(--white); font-size: 9.2px; white-space: nowrap; }
  .footer-links span.sep { margin: 0 8px; }
  .copyright { position: absolute; left: 550px; top: 1136px; color: var(--white); font-size: 9px; }
</style>
</head>
<body>
<div class="page">
  <header class="site-header">
    <div class="brand header-brand"><span class="brand-mark"></span><span>Brightwater<br>Civic Advisors</span></div>
    <a class="cta-button" href="#consult">BOOK A COMPLIMENTARY CONSULTATION</a>
    <nav class="main-nav">
      <a href="#" style="left:460px">ABOUT</a>
      <a href="#" style="left:524px">SERVICES &amp; TESTIMONIALS</a>
      <a href="#" style="left:690px">MEDIA &amp; IMPACT</a>
      <a href="#" class="is-current" style="left:809px">CONTACT</a>
    </nav>
  </header>

  <h1 class="page-title">Contact</h1>
  <div class="portrait" role="img" aria-label="Portrait photo of consultant Nora"></div>

  <h2 class="section-heading rates-heading">Rates</h2>
  <p class="section-text rates-text">Depending on the services requested, Nora offers an hourly rate, a package rate, or a retainer fee based on the scope and complexity of the project.</p>

  <h2 class="section-heading consult-heading" id="consult">Book a complimentary consultation</h2>
  <p class="section-text consult-text">Use the form below to tell Nora about your inquiry, and she will schedule a 30-minute meeting, phone call, or video chat to discuss your project outcomes.</p>

  <form class="contact-form">
    <div class="field" style="left:224px;top:600px;width:265px;height:36px">First name</div>
    <div class="field" style="left:502px;top:600px;width:265px;height:36px">Last name</div>
    <div class="field" style="left:224px;top:643px;width:265px;height:36px">Organization name</div>
    <div class="field" style="left:502px;top:643px;width:265px;height:36px">Email address</div>
    <div class="field" style="left:224px;top:687px;width:542px;height:36px">Subject</div>
    <div class="field field-message" style="left:224px;top:731px;width:542px;height:83px">Message</div>
    <div class="submit-button">SUBMIT</div>
  </form>

  <div class="footer-band"></div>
  <svg class="footer-shape" width="982" height="316" viewBox="0 0 982 316">
    <polygon points="0,142 491,54 982,142 982,316 0,316" fill="var(--footer-dark)"/>
  </svg>
  <footer>
    <div class="brand footer-brand"><span class="brand-mark"></span><span>Brightwater<br>Civic Advisors</span></div>
    <div class="footer-divider"></div>
    <div class="footer-menu-title">MENU</div>
    <div class="footer-links">ABOUT<span class="sep">|</span>SERVICES &amp; TESTIMONIALS<span class="sep">|</span>MEDIA &amp; IMPACT<span class="sep">|</span>CONTACT</div>
    <div class="copyright">Copyrights @ 2019 All Rights Reserved</div>
  </footer>
</div>
</body>
</html>
```